Business Card: RW Office Partners - Your organised problem solver

Business Name: RW Office Partners
Website: www.rwofficepartners.com.au
Email: marisol@rwofficepartners.com.au
Mobile: 61 482 907 236
Facebook: @rwofficepartners
Instrgram: @rwofficepartners

Brading Colours:
HEX
#986474
#ddccd3
#7a8498
#c9d8e4
#000000
#ffffff

Tag Line: Your organised problem solver

Link to DRAFT website:
https://deskhelpcollective.wixsite.com/rw-office-partners

About Page from the website:
My name is Marisol Wrenfield, and I would love to assist you to become more productive in your day to day and achieve your business and personal goals.
My mission is to give you time, time to work on the important tasks of your business or to be able to spend more time with your family. I will take on the tasks you don’t have time for, don’t know well or simply don’t like to do.
I have an extensive background in Administration, Tender Coordination, Document Control, WHS and Quality Management working primarily in the Construction, Mining and Corporate World.
I am passionate about being organised, having order and making things in your life (and mine) easier! I love to watch something unfold and grow into something amazing! I am known for being the go-to problem solver, the organiser of all things, producing high standards of work even under pressure. I’m also a confident communicator, and I understand that you’re busy running your business.

Target Market(s)

Small to Medium Business who require assistance in their business by a virtual assistant.

Industry/Entity Type

Virtual Assistant

Contact Information for Business Card

Mobile: 61 482 907 236

Font styles to use
Sans Serif

Colors
ffffff

Requirements
Must have
• Branding Colours as outlined.
Contact Details as outlined.
Logo as provided.
Proper contact details - mobile, facebook, instragm, website.
Simple, Elegant, very clean looking.
Should not have
• Note cute with pictures.
Not too girly as still want to market to construction companies.

```html
<!DOCTYPE html>
<html lang="en">
<head>
<meta charset="utf-8">
<title>RW Office Partners – Business Card</title>
<link rel="stylesheet" href="https://fonts.googleapis.com/css2?family=Montserrat:wght@500;600;700&family=Arimo:wght@400&display=swap">
<style>
  :root {
    --rose: #986474;
    --rose-light: #ddccd3;
    --slate: #7a8498;
    --mist: #c9d8e4;
    --white: #ffffff;
    --card: #1f2023;
    --card-tone: #232428;
    --stage: #2e2e30;
    --rule: #55575c;
  }
  * { box-sizing: border-box; margin: 0; padding: 0; }
  html, body { width: 1200px; height: 1108px; overflow: hidden; background: var(--stage); }
  .canvas {
    position: relative; width: 1200px; height: 1108px;
    display: flex; justify-content: center; align-items: center; gap: 60px;
  }
  .card {
    position: relative; width: 440px; height: 720px;
    background: var(--card); border-radius: 22px; overflow: hidden;
    box-shadow: 0 14px 30px rgba(0,0,0,.35);
  }

  /* Front */
  .card-front { display: flex; flex-direction: column; align-items: center; padding-top: 96px; }
  .brand-name {
    font-family: "Montserrat", sans-serif; font-weight: 600; text-transform: uppercase;
    color: var(--rose); font-size: 44px; line-height: 1.08; letter-spacing: 1px; text-align: center;
  }
  .holder-name {
    margin-top: 118px; font-family: "Montserrat", sans-serif; font-weight: 600;
    color: var(--rose); font-size: 23px; letter-spacing: .5px; text-transform: uppercase;
  }
  .divider { display: flex; align-items: center; gap: 8px; width: 300px; margin-top: 12px; }
  .divider .rule { flex: 1; height: 1px; background: var(--rule); }
  .icon-tile {
    width: 26px; height: 26px; background: var(--rose); border-radius: 4px;
    display: flex; align-items: center; justify-content: center;
  }
  .icon-ring {
    width: 28px; height: 28px; border: 1.5px solid var(--slate); border-radius: 50%;
  }
  .contact-list { margin-top: 10px; text-align: center; font-family: "Arimo", sans-serif; font-size: 19px; line-height: 1.42; }
  .contact-phone, .contact-email { color: var(--white); }
  .contact-web { color: var(--rose); }
  .contact-web .domain-lead { color: var(--slate); }
  .divider-social { margin-top: 12px; }
  .social-handle { margin-top: 8px; font-family: "Arimo", sans-serif; font-size: 19px; color: var(--white); }

  /* Back */
  .backdrop-area {
    position: absolute; left: 0; top: 0; width: 100%; height: 64%;
    background: linear-gradient(180deg, var(--card-tone), var(--card));
  }
  .back-brand {
    position: absolute; left: 0; right: 0; top: 395px; text-align: center;
    font-family: "Montserrat", sans-serif; font-weight: 600; text-transform: uppercase;
    color: var(--rose); font-size: 20px; letter-spacing: 1px;
  }
  .tagline {
    position: absolute; left: 0; right: 0; bottom: 110px; text-align: center;
    font-family: "Montserrat", sans-serif; font-weight: 700; text-transform: uppercase;
    color: var(--white); font-size: 22px; line-height: 1.22;
  }
</style>
</head>
<body>
<main class="canvas">
  <section class="card card-front" aria-label="Card front">
    <h1 class="brand-name">RW Office<br>Partners</h1>
    <p class="holder-name">Marisol Wrenfield</p>
    <div class="divider">
      <span class="rule"></span>
      <span class="icon-tile" aria-label="Phone">
        <svg width="16" height="16" viewBox="0 0 24 24"><path fill="#1f2023" d="M6.6 10.8a15 15 0 0 0 6.6 6.6l2.2-2.2a1 1 0 0 1 1-.25 11.4 11.4 0 0 0 3.6.57 1 1 0 0 1 1 1V20a1 1 0 0 1-1 1A17 17 0 0 1 3 4a1 1 0 0 1 1-1h3.5a1 1 0 0 1 1 1c0 1.25.2 2.45.57 3.57a1 1 0 0 1-.25 1z"/></svg>
      </span>
      <span class="icon-tile" aria-label="Email">
        <svg width="16" height="16" viewBox="0 0 24 24"><rect x="2" y="5" width="20" height="14" rx="1.5" fill="#1f2023"/><path d="M3 6l9 7 9-7" fill="none" stroke="#986474" stroke-width="1.8"/></svg>
      </span>
      <span class="icon-tile" aria-label="Location">
        <svg width="16" height="16" viewBox="0 0 24 24"><path fill="#1f2023" d="M12 2a7 7 0 0 0-7 7c0 5.2 7 13 7 13s7-7.8 7-13a7 7 0 0 0-7-7zm0 9.5A2.5 2.5 0 1 1 12 6.5a2.5 2.5 0 0 1 0 5z"/></svg>
      </span>
      <span class="rule"></span>
    </div>
    <div class="contact-list">
      <p class="contact-phone">61 482 907 236</p>
      <p class="contact-email">marisol@rwofficepartners.com.au</p>
      <p class="contact-web"><span class="domain-lead">www.rwofficepartners</span>.com.au</p>
    </div>
    <div class="divider divider-social">
      <span class="rule"></span>
      <span class="icon-ring" aria-label="Social profile"></span>
      <span class="icon-ring" aria-label="Social profile"></span>
      <span class="rule"></span>
    </div>
    <p class="social-handle">@rwofficepartners</p>
  </section>

  <section class="card card-back" aria-label="Card back">
    <div class="backdrop-area" role="img" aria-label="Faint repeating brand pattern area"></div>
    <p class="back-brand">RW Office Partners</p>
    <p class="tagline">Your organised<br>problem solver</p>
  </section>
</main>
</body>
</html>
```